Specialised investor in e-mobility and energy wants business card design

We need a business card design that fits our existing corporate design. <The look and feel must be 'sharp'/'clean', dynamic, communicate momentum, professionalism etc (as one would imagine from a firm in the financial sector). We like the idea of a reverse-side of the card that includes the logo, and the name and contact details on the other. We expect the deliverable to be whatever format might be required to be able to get cards printed directly by a service such as kelmo press. Our website is www.zub.capital

```html
<!DOCTYPE html>
<html lang="en">
<head>
<meta charset="utf-8">
<title>ZUB Capital – Business Card</title>
<link rel="stylesheet" href="https://fonts.googleapis.com/css2?family=Montserrat:wght@400;500;800&display=swap">
<style>
  :root {
    --page-bg: #2a2c2e;
    --card-white: #ffffff;
    --green-dark: #2e4d20;
    --green-back: #33572a;
    --green-pattern: #2c4c23;
    --green-light: #76b043;
    --ink: #3a3a3a;
  }
  * { box-sizing: border-box; margin: 0; padding: 0; }
  html, body { width: 1200px; height: 900px; overflow: hidden; }
  body {
    background: var(--page-bg);
    font-family: "Montserrat", sans-serif;
    display: flex; flex-direction: column; align-items: center; justify-content: center; gap: 56px;
  }
  .card {
    position: relative; width: 640px; height: 366px;
    border-radius: 22px; overflow: hidden;
    box-shadow: 0 10px 28px rgba(0,0,0,.45);
  }

  /* Front */
  .card-front { background: var(--card-white); color: var(--ink); }
  .holder { position: absolute; left: 40px; top: 46px; }
  .holder-name { font-weight: 800; font-size: 27px; letter-spacing: 1px; color: var(--green-dark); text-transform: uppercase; }
  .holder-name .surname { color: var(--green-light); }
  .holder-role { font-size: 14px; font-style: italic; margin-top: 2px; }
  .divider { position: absolute; left: 40px; right: 80px; top: 132px; height: 1px; background: var(--green-dark); }
  .contacts { position: absolute; left: 40px; top: 152px; list-style: none; }
  .contacts li { display: flex; align-items: center; gap: 10px; font-size: 14px; font-style: italic; margin-bottom: 10px; }
  .contacts svg { width: 14px; height: 14px; fill: var(--green-light); flex: none; }
  .brand-front {
    position: absolute; right: 44px; top: 180px;
    font-weight: 500; font-size: 42px; color: var(--green-dark); letter-spacing: .5px;
  }
  .address { position: absolute; right: 40px; bottom: 44px; text-align: right; font-size: 14px; line-height: 1.4; }
  .base-band { position: absolute; left: 300px; width: 180px; bottom: 0; height: 10px; background: var(--green-dark); }

  /* Back */
  .card-back { background: var(--green-back); }
  .pattern-field {
    position: absolute; inset: 0;
    background: linear-gradient(135deg, var(--green-back), var(--green-pattern));
  }
  .brand-back {
    position: absolute; inset: 0; display: flex; align-items: center; justify-content: center;
    font-weight: 500; font-size: 54px; color: var(--card-white); letter-spacing: .5px;
  }
</style>
</head>
<body>

  <section class="card card-front" aria-label="Business card front">
    <div class="holder">
      <p class="holder-name">Martin <span class="surname">Okoye</span></p>
      <p class="holder-role">Director/Founder</p>
    </div>
    <div class="divider"></div>
    <ul class="contacts">
      <li>
        <svg viewBox="0 0 24 24" aria-hidden="true"><path d="M6.6 10.8a15 15 0 0 0 6.6 6.6l2.2-2.2c.3-.3.7-.4 1-.2 1.1.4 2.3.6 3.6.6.6 0 1 .4 1 1V20c0 .6-.4 1-1 1A17 17 0 0 1 3 4c0-.6.4-1 1-1h3.5c.6 0 1 .4 1 1 0 1.3.2 2.5.6 3.6.1.3 0 .7-.2 1z"/></svg>
        123-480-2291
      </li>
      <li>
        <svg viewBox="0 0 24 24" aria-hidden="true"><path d="M2 5h20v14H2zm2 2v.5l8 5 8-5V7l-8 5z"/></svg>
        info@zub.capital
      </li>
      <li>
        <svg viewBox="0 0 24 24" aria-hidden="true"><path d="M12 2a10 10 0 1 0 0 20 10 10 0 0 0 0-20zm-1 17.9A8 8 0 0 1 4.1 11H7c0 3 1.5 6.1 4 8.9zM13 4.1A8 8 0 0 1 19.9 11H17c0-3-1.5-6.1-4-6.9z"/></svg>
        www.zub.capital
      </li>
    </ul>
    <p class="brand-front">ZUB Capital</p>
    <p class="address">1234 Street Name<br>Country Name AB 5748</p>
    <div class="base-band"></div>
  </section>

  <section class="card card-back" aria-label="Business card back">
    <div class="pattern-field" role="img" aria-label="Repeating tone-on-tone brand pattern in dark greens"></div>
    <p class="brand-back">ZUB Capital</p>
  </section>

</body>
</html>
```